Dusty Spur Outfitters Home Page

I need a logo and page design for my home page, maybe some background color suggestions to go with it. I want the logo to project "vintage" and "western wear" but not be your typical trite western saddle and gun type thing.
http://www.dustyspuroutfitters.example/store/cart.php
Not looking for page coding just logo and other design elements to lay in over the site's template to make it "pop"
Reason: Have to finalize the design.
Target Market(s)
My customers are 70/30 men to women.
Industry/Entity Type
Gun

```html
<!DOCTYPE html>
<html lang="en">
<head>
<meta charset="utf-8">
<title>Dusty Spur Outfitters – Home</title>
<link href="https://fonts.googleapis.com/css2?family=Ubuntu:wght@400;500;700&display=swap" rel="stylesheet">
<style>
:root{
  --black:#000;
  --header:#1a1a1a;
  --red:#d8141f;
  --red-dark:#a20d15;
  --red-deep:#7d0a10;
  --teal:#3fc3cc;
  --teal-dark:#0e8791;
  --teal-ink:#0f4d55;
  --white:#fff;
  --grey:#8a8a8a;
  --line:#2b2b2b;
}
*{margin:0;padding:0;box-sizing:border-box}
html,body{width:784px;height:1200px;overflow:hidden;background:var(--black);font-family:"Ubuntu",sans-serif;color:var(--white)}
.page{position:relative;width:784px;height:1200px}
.abs{position:absolute}
.header{left:0;top:0;width:784px;height:80px;background:radial-gradient(circle at 40% 30%,#2a2a2a,#0d0d0d 70%)}
.logo{left:86px;top:30px;font-size:24px;font-weight:700;color:var(--red);letter-spacing:.3px}
.cart-label{left:664px;top:18px;font-size:10px;line-height:12px}
.cart-label span{color:var(--teal);display:block}
.search{left:566px;top:50px;width:138px;height:18px;border:1px solid #555;border-radius:9px;background:#000;font-size:7px;padding:5px 9px}
.nav-band{left:0;top:74px;width:784px;height:37px;background:var(--red-dark)}
.nav{left:76px;top:74px;width:632px;height:33px;background:var(--red);display:flex}
.nav a{color:var(--white);text-decoration:none;font-size:10.5px;font-weight:500;line-height:33px;text-align:center;border-right:1px solid var(--red-dark)}
.nav a:last-child{border:0}
.hero{left:76px;top:107px;width:632px;height:262px;border-radius:0 0 12px 12px;background:linear-gradient(180deg,#8ee0e4 0%,var(--teal) 55%,var(--teal-dark) 100%);overflow:hidden}
.hero-photo{position:absolute;left:328px;top:0;width:270px;height:262px;background:linear-gradient(160deg,#5bd0d6,#3b8c94 60%,#27666d)}
.hero h1{position:absolute;left:40px;top:72px;font-size:22px;font-weight:700}
.hero h2{position:absolute;left:41px;top:102px;font-size:15px;font-weight:500;color:var(--teal-ink)}
.hero p{position:absolute;left:42px;top:124px;width:270px;font-size:7.5px;line-height:13px;color:#e8fbfc}
.dots{position:absolute;left:42px;top:159px;display:flex;gap:3px}
.dots i{width:7px;height:7px;border-radius:50%;background:var(--white)}
.welcome{left:80px;top:400px;width:624px;text-align:center}
.welcome h2{font-size:18px;font-weight:400}
.welcome p{margin-top:8px;font-size:7.5px;line-height:14px;color:var(--grey)}
.rule{left:80px;top:497px;width:624px;height:1px;background:var(--line)}
.featured{left:80px;top:524px;font-size:16px;color:var(--red)}
.grid{left:80px;width:624px;height:183px;border:1px solid var(--line);display:flex}
.card{width:156px;border-right:1px solid var(--line);text-align:center}
.card:last-child{border:0}
.thumb{height:108px}
.card h3{margin-top:11px;font-size:10px;font-weight:400}
.card p{font-size:7px;color:var(--grey);margin-top:3px}
.btn{display:inline-block;margin-top:6px;width:84px;height:22px;line-height:22px;background:var(--red);font-size:9px;font-weight:500;border:1px solid #ff3b44}
.footer{left:0;top:984px;width:784px;height:176px;background:radial-gradient(ellipse at 50% 40%,#c8161f,var(--red-dark) 80%)}
.col{top:1016px}
.col h4{font-size:10.5px;font-weight:700;margin-bottom:6px}
.col a{display:block;font-size:7px;font-weight:500;line-height:17px;color:var(--white);text-decoration:none}
.email{left:424px;top:1037px;width:122px;height:18px;background:var(--white);color:#777;font-size:7px;padding:5px 8px}
.email-go{left:546px;top:1037px;width:20px;height:18px;background:#111}
.ship{left:424px;top:1074px;width:150px}
.ship h4{font-size:10.5px;font-weight:700}
.ship p{margin-top:4px;font-size:7px;line-height:12px;color:#f2b4b7}
.touch{left:596px;top:1016px;font-size:10px;font-weight:500}
.pay{left:598px;top:1072px;font-size:7px}
.bottom{left:0;top:1160px;width:784px;height:40px;background:var(--red-deep)}
.copy{left:85px;top:1177px;font-size:7px;color:#f0c6c8}
</style>
</head>
<body>
<div class="page">
  <div class="abs header"></div>
  <div class="abs logo">Dusty Spur Outfitters</div>
  <svg class="abs" style="left:636px;top:16px" width="24" height="24" viewBox="0 0 24 24"><rect x="1" y="7" width="22" height="16" rx="2" fill="#3fc3cc"/><path d="M7 9V5a5 5 0 0 1 10 0v4" stroke="#3fc3cc" stroke-width="2.5" fill="none"/></svg>
  <div class="abs cart-label">0 Items<span>0.00 $</span></div>
  <div class="abs search">Search</div>
  <svg class="abs" style="left:688px;top:54px" width="10" height="10" viewBox="0 0 10 10"><circle cx="4" cy="4" r="3" stroke="#fff" stroke-width="1.3" fill="none"/><path d="M6.3 6.3 9 9" stroke="#fff" stroke-width="1.4"/></svg>

  <div class="abs nav-band"></div>
  <nav class="abs nav">
    <a style="width:81px">HOME</a><a style="width:84px">ABOUT US</a><a style="width:86px">PRODUCTS</a><a style="width:74px">RETURN</a><a style="width:80px">SHIPPING</a><a style="width:64px">SIZING</a><a style="width:63px">LINKS</a><a style="width:100px">CONTACT</a>
  </nav>

  <section class="abs hero">
    <div class="hero-photo" role="img" aria-label="Model in a black cowboy hat, white shirt and paisley vest"></div>
    <h1>VINTAGE WESTERN WEARING</h1>
    <h2>SUSPENDISSE VULPUTATE ALIQUAM</h2>
    <p>Etiam est nunc venenatis in tristique eu imperdiet ac nisl Cum sociis natoque penatibus et magnis dis parturient montes</p>
    <div class="dots"><i></i><i></i><i></i><i></i></div>
  </section>

  <section class="abs welcome">
    <h2>Welcome to Dusty Spur Outfitters Mainpage</h2>
    <p>Etiam est nunc venenatis in tristique eu imperdiet ac nisl Cum sociis natoque penatibus et magnis dis parturient montes nascetur ridiculus mus In iaculis facilisis massa Etiam eu urna Sed porta Suspendisse quam leo molestie sed luctus quis feugiat in pede Fusce tellus Sed metus augue convallis et vehicula ut pulvinar eu ante Integer orci tellus tristique vitae consequat nec porta vel lectus Nulla sit amet diam</p>
  </section>
  <div class="abs rule"></div>
  <h2 class="abs featured">Featured Products</h2>

  <div class="abs grid" style="top:556px">
    <div class="card"><div class="thumb" role="img" aria-label="Man in black western suit and white hat" style="background:linear-gradient(#e6e6e6,#bdbdbd)"></div><h3>Product Name</h3><p>Erat fermentum vel congue id eu</p><span class="btn">Add to Cart</span></div>
    <div class="card"><div class="thumb" role="img" aria-label="Tan leather cowboy boot" style="background:radial-gradient(circle,#6b4a30 0 18%,#000 40%)"></div><h3>Product Name</h3><p>Erat fermentum vel congue id eu</p><span class="btn">Add to Cart</span></div>
    <div class="card"><div class="thumb" role="img" aria-label="Suede fringe jacket" style="background:linear-gradient(90deg,#8fd0ec,#a47a52 45%,#8fd0ec)"></div><h3>Product Name</h3><p>Erat fermentum vel congue id eu</p><span class="btn">Add to Cart</span></div>
    <div class="card"><div class="thumb" role="img" aria-label="Cream and blue western shirt" style="background:linear-gradient(#9fd4ea,#f0e6d2 50%,#e8dcc4)"></div><h3>Product Name</h3><p>Erat fermentum vel congue id eu</p><span class="btn">Add to Cart</span></div>
  </div>
  <div class="abs grid" style="top:748px">
    <div class="card"><div class="thumb" role="img" aria-label="Western print blanket" style="background:radial-gradient(circle,#5a4a3a 0 28%,#000 45%)"></div><h3>Product Name</h3><p>Erat fermentum vel congue id eu</p><span class="btn">Add to Cart</span></div>
    <div class="card"><div class="thumb" role="img" aria-label="Blue denim jeans" style="background:linear-gradient(90deg,#cfcfcf,#5b6d80 40%,#5b6d80 60%,#cfcfcf)"></div><h3>Product Name</h3><p>Erat fermentum vel congue id eu</p><span class="btn">Add to Cart</span></div>
    <div class="card"><div class="thumb" role="img" aria-label="Leather tote bags" style="background:radial-gradient(circle,#4a3424 0 22%,#fff 40%)"></div><h3>Product Name</h3><p>Erat fermentum vel congue id eu</p><span class="btn">Add to Cart</span></div>
    <div class="card"><div class="thumb" role="img" aria-label="Red embroidered women's western shirt" style="background:linear-gradient(#7a2a26,#b01e1e 60%,#8d1616)"></div><h3>Product Name</h3><p>Erat fermentum vel congue id eu</p><span class="btn">Add to Cart</span></div>
  </div>

  <footer class="abs footer"></footer>
  <div class="abs col" style="left:82px"><h4>COMPANY</h4><a>ABOUT US</a><a>WHY US</a><a>ORDER NOW</a><a>CATEGORIES</a><a>SITEMAP</a></div>
  <div class="abs col" style="left:173px"><h4>PRODUCTS</h4><a>ETIAM EST NUNC</a><a>VENENATIS IN TRISTIQUE</a><a>EU IMPERDIET AC NISL</a><a>CUM SOCIIS NATOQUE</a><a>PENATIBUS ET MAGNIS</a></div>
  <div class="abs col" style="left:304px"><h4>SUPPORT</h4><a>ORDER &amp; DELIVERY</a><a>FAQ</a><a>CONTACT US</a><a>SUPPORT</a><a>TESTIMONIALS</a></div>
  <div class="abs col" style="left:424px"><h4>NEWSLETERS SIGN UP</h4></div>
  <div class="abs email">Email address</div>
  <div class="abs email-go"><svg width="20" height="18"><path d="M9 6l4 3-4 3z" fill="#fff"/></svg></div>
  <div class="abs ship"><h4>FREE SHIPPING NOW</h4><p>Ut nisi erat fermentum vel congue id euis-mod in elit Fusce ultricies orci</p></div>
  <div class="abs touch">GET IN TOUCH</div>
  <svg class="abs" style="left:596px;top:1034px" width="84" height="20"><g fill="#fff"><circle cx="10" cy="10" r="9"/><circle cx="31" cy="10" r="9"/><circle cx="52" cy="10" r="9"/><circle cx="73" cy="10" r="9"/></g></svg>
  <div class="abs pay">Make Payment</div>
  <svg class="abs" style="left:598px;top:1085px" width="102" height="14"><g fill="#eee"><rect x="0" width="22" height="14" rx="2"/><rect x="26" width="22" height="14" rx="2"/><rect x="52" width="22" height="14" rx="2"/><rect x="78" width="22" height="14" rx="2"/></g></svg>

  <div class="abs bottom"></div>
  <div class="abs copy">© 2014 Company Name.&nbsp; All right reserved.&nbsp; Term of Use</div>
</div>
</body>
</html>
```